Harbor Crestline (Business Card Design)

Need business cards designed. Something modern, chic, and sleek. Mabye the back of the card should be the navy blue that is in the logo and then just the logo on the back.

Target Market(s)

Those in the hotel, office, and renovation industry

Contact Information for Business Card

1. Logo 2. Dorian Fenwick 3. CEO/Founder 4. Phone: (833) HarbCre / (833) 427-2731 5. Email: dorian@theharborcrestline.com 6. Website: www.theharborcrestline.com

Font styles to use
Other font styles liked:
• Look at the logo font and base the font for everything else off of that.

Colors
0054AA
0677BA
7BADD7
CADEEF
E8F1F8

Requirements
Must have
• Colors that are associated in the logo
Nice to have
• Sleek modern clean and chic design.

```html
<!DOCTYPE html>
<html lang="en">
<head>
<meta charset="utf-8">
<title>Harbor Crestline — Business Cards</title>
<link rel="stylesheet" href="https://fonts.googleapis.com/css2?family=Montserrat:wght@500&family=Poppins:wght@400;500;700&display=swap">
<style>
  :root {
    --page: #ffffff;
    --navy-deep: #060b26;
    --navy: #0b1552;
    --navy-mid: #0a1346;
    --gold: #c9a448;
    --white: #ffffff;
  }
  * { box-sizing: border-box; margin: 0; padding: 0; }
  html, body {
    width: 684px; height: 1200px; overflow: hidden;
    background: var(--page);
  }
  .sheet {
    width: 684px; height: 1200px;
    display: flex; align-items: center; justify-content: center; gap: 44px;
  }
  .card {
    position: relative;
    width: 290px; height: 507px;
    overflow: hidden;
    background:
      radial-gradient(ellipse 90% 45% at 50% 55%, var(--navy) 0%, var(--navy-mid) 45%, rgba(10,19,70,0) 100%),
      linear-gradient(180deg, var(--navy-deep) 0%, var(--navy-mid) 50%, var(--navy-deep) 100%);
    box-shadow: 0 12px 36px rgba(0,0,0,0.22);
    color: var(--white);
  }

  /* Front */
  .brand {
    position: absolute; left: 0; right: 0; top: 196px;
    display: flex; flex-direction: column; align-items: center;
  }
  .brand__mark {
    width: 18px; height: 18px; background: var(--gold); margin-bottom: 22px;
  }
  .brand__name {
    font-family: "Montserrat", sans-serif; font-weight: 500;
    font-size: 30px; line-height: 1.15; letter-spacing: 2.5px;
    text-transform: uppercase; text-align: center;
    color: var(--white);
  }
  .brand__line { display: block; }
  .brand__url {
    margin-top: 22px;
    font-family: "Poppins", sans-serif; font-weight: 700;
    font-size: 9.5px; letter-spacing: 2px; color: var(--white);
  }

  /* Back */
  .contact { position: absolute; left: 35px; top: 228px; font-family: "Poppins", sans-serif; }
  .contact__name {
    font-weight: 700; font-size: 27px; line-height: 1.1; letter-spacing: -0.2px;
    text-transform: uppercase; white-space: nowrap;
  }
  .contact__surname { color: var(--gold); }
  .contact__role { color: var(--gold); font-size: 14px; font-weight: 400; margin-top: 1px; }
  .contact__list { list-style: none; margin-top: 24px; }
  .contact__list li { line-height: 24px; font-weight: 500; }
  .contact__phone { font-size: 15px; }
  .contact__web { font-size: 12.5px; }
</style>
</head>
<body>
<main class="sheet">
  <section class="card card--front" aria-label="Card front">
    <div class="brand">
      <span class="brand__mark"></span>
      <h1 class="brand__name"><span class="brand__line">Harbor</span><span class="brand__line">Crestline</span></h1>
      <p class="brand__url">www.theharborcrestline.com</p>
    </div>
  </section>

  <section class="card card--back" aria-label="Card back">
    <div class="contact">
      <h2 class="contact__name">Dorian <span class="contact__surname">Fenwick</span></h2>
      <p class="contact__role">CEO/Founder</p>
      <ul class="contact__list">
        <li class="contact__phone">(833) HarbCre</li>
        <li class="contact__phone">(833) 427-2731</li>
        <li class="contact__web">dorian@theharborcrestline.com</li>
        <li class="contact__web">www.theharborcrestline.com</li>
      </ul>
    </div>
  </section>
</main>
</body>
</html>
```